Business Card Design for Occupational Medicine Start Up Company

We need to design a professional business card. We are a healthcare company providing occupational medicine services to blue collar industries. We are professional, efficient and high quality service providers.

Target Market(s)

Blue Collar Industry: Shipbuilding, Ports, Trucking Companies; The Executives and Safety Officers for these companies

Industry/Entity Type

Healthcare

Contact Information for Business Card

Logo, Name, Title, Email, Phone

Other font styles liked:
• Please match our Brand Guide

Requirements
Must have
• Our Company Colors and Logo

```html
<!DOCTYPE html>
<html lang="en">
<head>
<meta charset="utf-8">
<title>Business Card – CrewSafe Health</title>
<link rel="stylesheet" href="https://fonts.googleapis.com/css2?family=Arimo:wght@400;700&display=swap">
<style>
  :root {
    --navy: #2b3585;
    --orange: #f5ac45;
    --sky: #27a9e1;
    --blush: #f3c9c4;
    --frost-light: #f7f7f8;
    --frost-dark: #e6e8ec;
    --page: #d9dce1;
    --white: #ffffff;
  }
  html, body {
    margin: 0;
    width: 1200px;
    height: 900px;
    overflow: hidden;
    background: var(--page);
    font-family: "Arimo", Arial, sans-serif;
  }
  .business-card {
    position: absolute;
    left: 100px;
    top: 141px;
    width: 1000px;
    height: 618px;
    background: linear-gradient(135deg, var(--frost-dark), var(--frost-light) 60%, var(--frost-dark));
    box-shadow: 0 12px 40px rgba(0, 0, 0, 0.18);
    overflow: hidden;
  }
  .card-shape {
    position: absolute;
    inset: 0;
    width: 1000px;
    height: 618px;
  }
  .holder {
    position: absolute;
    left: 58px;
    top: 66px;
    color: var(--white);
  }
  .holder-name {
    margin: 0;
    font-size: 41px;
    font-weight: 700;
    letter-spacing: 0.5px;
    line-height: 1;
  }
  .holder-title {
    margin: 6px 0 0;
    font-size: 27px;
    font-weight: 400;
  }
  .contact-list {
    position: absolute;
    left: 58px;
    top: 234px;
    margin: 0;
    padding: 0;
    list-style: none;
    color: var(--white);
    font-size: 27px;
  }
  .contact-item {
    display: flex;
    align-items: center;
    height: 36.5px;
  }
  .contact-icon {
    width: 26px;
    height: 26px;
    margin-right: 9px;
    flex: none;
  }
  .brand {
    position: absolute;
    left: 534px;
    top: 380px;
    width: 400px;
    text-align: center;
  }
  .brand-dot {
    display: block;
    width: 96px;
    height: 96px;
    margin: 0 auto 34px;
    border-radius: 50%;
    background: var(--navy);
  }
  .brand-name {
    margin: 0;
    color: var(--navy);
    font-size: 44px;
    font-weight: 700;
    letter-spacing: 0.5px;
    line-height: 1;
  }
</style>
</head>
<body>
  <div class="business-card">
    <svg class="card-shape" viewBox="0 0 1000 618" aria-hidden="true">
      <path d="M735 0 L597 249 L515 395 C476 470 406 580 327 618" fill="none" stroke="var(--sky)" stroke-width="8"/>
      <path d="M715 0 L577 249 L495 395 C456 470 386 580 307 618" fill="none" stroke="var(--blush)" stroke-width="5"/>
      <path d="M703 0 L565 249 L483 395 C444 470 374 580 295 618" fill="none" stroke="var(--orange)" stroke-width="8"/>
      <path d="M0 0 H689 L551 249 L469 395 C430 470 360 580 281 618 H0 Z" fill="var(--navy)"/>
      <circle cx="547" cy="345" r="92" fill="var(--navy)"/>
    </svg>

    <div class="holder">
      <h1 class="holder-name">DANIEL MORROW</h1>
      <p class="holder-title">Managing Director</p>
    </div>

    <ul class="contact-list">
      <li class="contact-item">
        <svg class="contact-icon" viewBox="0 0 24 24" aria-hidden="true">
          <path d="M6.6 10.8a15 15 0 0 0 6.6 6.6l2.2-2.2a1 1 0 0 1 1-.25 11.4 11.4 0 0 0 3.6.6 1 1 0 0 1 1 1V20a1 1 0 0 1-1 1A17 17 0 0 1 3 4a1 1 0 0 1 1-1h3.5a1 1 0 0 1 1 1c0 1.25.2 2.45.6 3.6a1 1 0 0 1-.25 1z" fill="none" stroke="var(--white)" stroke-width="1.8"/>
        </svg>
        044-987 654 321
      </li>
      <li class="contact-item">
        <svg class="contact-icon" viewBox="0 0 24 24" aria-hidden="true">
          <rect x="2" y="5" width="20" height="14" fill="var(--white)"/>
          <path d="M2 5 L12 13 L22 5 M2 19 L9 11 M22 19 L15 11" fill="none" stroke="var(--navy)" stroke-width="1.5"/>
        </svg>
        hello@crewsafehealth.com
      </li>
      <li class="contact-item">
        <svg class="contact-icon" viewBox="0 0 24 24" aria-hidden="true">
          <g fill="none" stroke="var(--white)" stroke-width="1.6">
            <circle cx="12" cy="12" r="10"/>
            <ellipse cx="12" cy="12" rx="4.5" ry="10"/>
            <path d="M2 12 H22 M4 7 H20 M4 17 H20"/>
          </g>
        </svg>
        www.crewsafehealth.com
      </li>
    </ul>

    <div class="brand">
      <span class="brand-dot"></span>
      <p class="brand-name">CREWSAFE HEALTH</p>
    </div>
  </div>
</body>
</html>
```